Building company buisness cards

We are looking for a sharp modern new look for our business cards.
We are a New Zealand based company that specialises in house and land packages.
We have attached a photo of the current logo and would like to see if it can be improved somehow if needed.
We are open to any colours but we have chosen green at this stage.
Feel free to change the font and make the logo smarter looking.
Play with the colours and see what looks best.

We want a card that looks so good know one will want to throw it away!

Target Market(s)

Home buyers

Industry/Entity Type

Building

Contact Information for Business Card

Derek Tolvane
0217394062
dtolvane@quillmarkhomesteads.co.nz
quillmarkhomesteads.co.nz

Font styles to use
Serif
Sans Serif

Colors

Designer to choose colors to be used in the design.

Requirements
Must have
• Logo and company name on one side, details on the other side
Nice to have
• Color codes for the original green are HEX #4a8028, RGB(74,128,40), CMYK(42,0,69,50)
• Round corners, Raised and/or spot UV

```html
<!DOCTYPE html>
<html lang="en">
<head>
<meta charset="utf-8">
<title>Quillmark Homesteads — Business Cards</title>
<link rel="stylesheet" href="https://fonts.googleapis.com/css2?family=Nunito:wght@900&family=Cabin:wght@400&display=swap">
<style>
  :root {
    --backdrop: #2b2b2b;
    --brand-green: #4a8028;
    --brand-green-bright: #5cae16;
    --brand-green-soft: #56921f;
    --paper: #ffffff;
    --card-dark: #252525;
    --silver: #dcdcdc;
  }
  * { margin: 0; padding: 0; box-sizing: border-box; }
  html, body {
    width: 1125px;
    height: 1200px;
    overflow: hidden;
    background: var(--backdrop);
  }
  .canvas {
    position: relative;
    width: 1125px;
    height: 1200px;
  }
  .card {
    position: absolute;
    width: 470px;
    height: 822px;
    border-radius: 22px;
    overflow: hidden;
  }

  /* Details side */
  .card-front { left: 64px; top: 62px; background: var(--paper); }
  .card-front .card-ground {
    position: absolute; inset: 0;
    width: 100%; height: 100%;
  }
  .brand-name {
    position: absolute;
    left: 0; right: 0;
    top: 150px;
    text-align: center;
    font-family: "Nunito", sans-serif;
    font-weight: 900;
    font-size: 46px;
    line-height: 50px;
    letter-spacing: -0.5px;
    color: var(--brand-green);
  }
  .contact {
    position: absolute;
    left: 0; right: 0;
    top: 553px;
    text-align: center;
    font-family: "Cabin", sans-serif;
    font-weight: 400;
    color: var(--paper);
  }
  .contact-name {
    font-size: 27px;
    letter-spacing: 0.5px;
    text-transform: uppercase;
    line-height: 36px;
  }
  .contact-phone {
    margin-top: 28px;
    font-size: 21px;
    letter-spacing: 1px;
    line-height: 26px;
  }
  .contact-email,
  .contact-web {
    font-size: 16.5px;
    line-height: 26px;
  }

  /* Logo side */
  .card-back { left: 590px; top: 297px; background: var(--card-dark); }
  .brand-dot {
    position: absolute;
    left: 166px;
    top: 236px;
    width: 60px;
    height: 60px;
    border-radius: 50%;
    background: var(--brand-green);
  }
  .brand-vertical {
    position: absolute;
    left: 150px;
    top: 340px;
    writing-mode: vertical-rl;
    font-family: "Nunito", sans-serif;
    font-weight: 900;
    font-size: 44px;
    line-height: 44px;
    letter-spacing: -0.5px;
    color: var(--silver);
  }
</style>
</head>
<body>
<main class="canvas">

  <section class="card card-front" aria-label="Details side">
    <svg class="card-ground" viewBox="0 0 470 822" preserveAspectRatio="none" aria-hidden="true">
      <defs>
        <linearGradient id="chevron-glow" x1="0" y1="0" x2="0" y2="1">
          <stop offset="0" stop-color="var(--brand-green-soft)"/>
          <stop offset="1" stop-color="var(--brand-green-bright)"/>
        </linearGradient>
      </defs>
      <rect x="0" y="0" width="470" height="822" fill="var(--brand-green)"/>
      <polygon points="0,300 470,300 470,345 262,495 235,505 208,495 0,345" fill="url(#chevron-glow)"/>
      <polygon points="0,0 470,0 470,312 258,452 235,460 212,452 0,312" fill="var(--paper)"/>
    </svg>

    <div class="brand-name">quillmark<br>homesteads.</div>

    <div class="contact">
      <p class="contact-name">Derek Tolvane</p>
      <p class="contact-phone">0217394062</p>
      <p class="contact-email">dtolvane@quillmarkhomesteads.co.nz</p>
      <p class="contact-web">quillmarkhomesteads.co.nz</p>
    </div>
  </section>

  <section class="card card-back" aria-label="Logo side">
    <span class="brand-dot" aria-hidden="true"></span>
    <div class="brand-vertical">quillmark<br>homesteads</div>
  </section>

</main>
</body>
</html>
```